Business Card Design

We need a business card designed for our new company. Prefer a black card with white logo & writing.

Contact Information for Business Card

Ted Galloway, address: 7-4812 Fernhollow Road, Abbotsford, BC, V3K 8R2, Office Phone: 604-712-3390, Cell: 604-947-2164, Email: ted@resinworkshub.ca

Colors

Designer to choose only greyscale colors for use in the design.

```html
<!DOCTYPE html>
<html lang="en">
<head>
<meta charset="utf-8">
<title>Resinworks Hub – Business Card</title>
<link rel="stylesheet" href="https://fonts.googleapis.com/css2?family=Montserrat:wght@400;700&family=Lato:wght@400&display=swap">
<style>
  :root {
    --backdrop: #3a3a3a;
    --card: #1b1b1b;
    --card-back: #1e1e1e;
    --emboss: #121212;
    --ink: #ffffff;
    --ink-soft: #d6d6d6;
    --tone-light: #6e6e6e;
    --tone-mid: #444444;
  }
  * { box-sizing: border-box; margin: 0; padding: 0; }
  html, body { width: 1200px; height: 895px; overflow: hidden; }
  body { background: var(--backdrop); position: relative; font-family: "Lato", sans-serif; }

  .card {
    position: absolute;
    width: 620px;
    height: 354px;
    border-radius: 22px;
    overflow: hidden;
    box-shadow: 0 10px 30px rgba(0,0,0,.45);
  }
  .card--back { left: 60px; top: 70px; background: var(--card-back); }
  .card--front { left: 520px; top: 470px; background: var(--card); }

  .brand {
    font-family: "Montserrat", sans-serif;
    font-weight: 700;
    letter-spacing: 1px;
    display: flex;
    align-items: center;
    gap: 12px;
    white-space: nowrap;
  }
  .brand__mark { width: 18px; height: 18px; }

  .card--back .brand {
    position: absolute; left: 50%; top: 50%;
    transform: translate(-50%, -50%);
    font-size: 40px; color: var(--emboss);
  }
  .card--back .brand__mark { background: var(--emboss); width: 26px; height: 26px; }

  .card--front .brand {
    position: absolute; right: 48px; top: 46px;
    font-size: 26px; color: var(--ink);
  }
  .card--front .brand__mark { background: var(--ink); }

  .tone-field {
    position: absolute; right: 0; top: 120px;
    width: 320px; height: 170px;
    background: linear-gradient(200deg, var(--tone-light) 0%, var(--tone-mid) 45%, rgba(27,27,27,0) 100%);
    opacity: .8;
  }

  .contact { position: absolute; left: 46px; top: 140px; color: var(--ink); }
  .contact__name { font-family: "Montserrat", sans-serif; font-weight: 700; font-size: 26px; line-height: 32px; }
  .contact__role { font-family: "Montserrat", sans-serif; font-size: 16px; line-height: 20px; color: var(--ink-soft); }
  .contact__list { list-style: none; margin-top: 14px; margin-left: 30px; }
  .contact__item { display: flex; align-items: center; gap: 10px; font-size: 16px; line-height: 22px; }
  .contact__icon { width: 15px; height: 15px; flex: none; }
  .contact__address { margin-left: 55px; margin-top: 8px; font-size: 16px; line-height: 21px; font-style: normal; }
</style>
</head>
<body>
  <section class="card card--back" aria-label="Card back">
    <div class="brand"><span class="brand__mark"></span>RESINWORKS HUB</div>
  </section>

  <section class="card card--front" aria-label="Card front">
    <div class="brand"><span class="brand__mark"></span>RESINWORKS HUB</div>

    <div class="tone-field" role="img" aria-label="Decorative layered grey graphic area"></div>

    <div class="contact">
      <h1 class="contact__name">Ted Galloway</h1>
      <p class="contact__role">President</p>
      <ul class="contact__list">
        <li class="contact__item">
          <svg class="contact__icon" viewBox="0 0 16 16"><path d="M2 5c0-2 2-3 6-3s6 1 6 3v1h-3V5H5v1H2zM4 7h8l2 7H2z" fill="var(--ink)"/></svg>
          604-712-3390
        </li>
        <li class="contact__item">
          <svg class="contact__icon" viewBox="0 0 16 16"><rect x="4" y="1" width="8" height="14" rx="1.5" fill="none" stroke="var(--ink)" stroke-width="1.5"/><circle cx="8" cy="12.5" r=".9" fill="var(--ink)"/></svg>
          604-947-2164
        </li>
        <li class="contact__item">
          <svg class="contact__icon" viewBox="0 0 16 16"><rect x="1" y="3" width="14" height="10" fill="var(--ink)"/><path d="M1 3l7 6 7-6" fill="none" stroke="var(--card)" stroke-width="1.3"/></svg>
          ted@resinworkshub.ca
        </li>
      </ul>
      <address class="contact__address">
        7-4812 Fernhollow Road,<br>Abbotsford, BC, V3K 8R2,
      </address>
    </div>
  </section>
</body>
</html>
```